RWT Fittings Ltd Business Cards

We need a business card with our business logo. We provide window and door installations on high-rises in west coast British Colombia, Canada.

I would like my business information and details on one side of the card, and the other side the company name with logo

Target Market(s)

General Contractors

Industry/Entity Type

Construction

Contact Information for Business Card

one side i want my company name and logo in the dark theme logo that i provided

Requirements
Must have
• Marco Peltieri, 16045518293, RWTFittings@mailbox-demo.com, 1407-5194 Linden Row Burnaby BC, V5H 2K9, Owner & Manager

```html
<!DOCTYPE html>
<html lang="en">
<head>
<meta charset="utf-8">
<title>RWT Fittings Ltd – Business Cards</title>
<link rel="stylesheet" href="https://fonts.googleapis.com/css2?family=Oswald:wght@700&family=Poppins:wght@400;600&display=swap">
<style>
  :root {
    --stage: #161616;
    --card: #232323;
    --card-back: #1b1b1b;
    --card-edge: #2c2c2c;
    --accent: #29a9e1;
    --text: #f2f2f2;
    --muted: #cfcfcf;
  }
  * { box-sizing: border-box; margin: 0; padding: 0; }
  html, body { width: 1200px; height: 900px; overflow: hidden; background: var(--stage); }
  .stage {
    width: 1200px; height: 900px;
    display: flex; flex-direction: column; align-items: center; justify-content: center; gap: 40px;
  }
  .card {
    width: 700px; height: 400px; position: relative; overflow: hidden;
    background: var(--card); border: 1px solid var(--card-edge);
    box-shadow: 0 18px 40px rgba(0,0,0,.55);
    font-family: "Poppins", sans-serif; color: var(--text);
  }
  .card-back { background: var(--card-back); }
  .pattern-area {
    position: absolute; inset: 0;
    background: linear-gradient(115deg, #141414 0%, #1e1e1e 40%, #4a4a4a 75%, #7a7a7a 100%);
  }
  .back-brand {
    position: absolute; right: 64px; bottom: 62px;
    display: flex; align-items: center; gap: 12px;
  }
  .back-brand .brand-square { width: 34px; height: 34px; }
  .back-brand .brand-name { font-size: 28px; color: var(--text); }
  .brand {
    position: absolute; top: 78px; left: 0; right: 0;
    display: flex; align-items: center; justify-content: center; gap: 16px;
  }
  .brand-square { width: 46px; height: 46px; background: var(--accent); flex: none; }
  .brand-name {
    font-family: "Poppins", sans-serif; font-weight: 600; font-size: 44px;
    letter-spacing: 2px; color: var(--accent); line-height: 1; white-space: nowrap;
  }
  .person {
    position: absolute; top: 190px; right: 380px; text-align: right;
  }
  .person-name {
    font-family: "Oswald", sans-serif; font-weight: 700; font-size: 40px;
    color: var(--accent); text-transform: uppercase; line-height: 1.05; white-space: nowrap;
  }
  .person-title { font-size: 16px; color: var(--muted); margin-top: 2px; white-space: nowrap; }
  .divider {
    position: absolute; top: 198px; left: 348px; width: 2px; height: 66px; background: var(--accent);
  }
  .contacts {
    position: absolute; top: 196px; left: 368px; list-style: none;
    font-size: 15px; line-height: 24px; color: var(--text);
  }
  .contacts li { display: flex; align-items: center; gap: 8px; white-space: nowrap; }
  .contacts svg { width: 14px; height: 14px; flex: none; }
  .contacts .web-domain { color: var(--accent); }
  .address {
    position: absolute; top: 318px; left: 0; right: 0;
    display: flex; align-items: center; justify-content: center; gap: 10px;
    font-size: 15px; color: var(--text);
  }
  .address-mark { width: 14px; height: 14px; background: var(--accent); }
</style>
</head>
<body>
<main class="stage">
  <section class="card card-back">
    <div class="pattern-area" role="img" aria-label="Repeating pattern of the company mark in glossy black and silver tones"></div>
    <div class="back-brand">
      <span class="brand-square"></span>
      <span class="brand-name">RWT FITTINGS LTD</span>
    </div>
  </section>

  <section class="card card-front">
    <div class="brand">
      <span class="brand-square"></span>
      <span class="brand-name">RWT FITTINGS LTD</span>
    </div>

    <div class="person">
      <div class="person-name">Marco Peltieri</div>
      <div class="person-title">Owner &amp; Manager</div>
    </div>

    <div class="divider"></div>

    <ul class="contacts">
      <li>
        <svg viewBox="0 0 24 24" fill="var(--accent)"><path d="M6.6 10.8a15.2 15.2 0 0 0 6.6 6.6l2.2-2.2a1 1 0 0 1 1-.25 11.4 11.4 0 0 0 3.6.57 1 1 0 0 1 1 1V20a1 1 0 0 1-1 1A17 17 0 0 1 3 4a1 1 0 0 1 1-1h3.5a1 1 0 0 1 1 1c0 1.25.2 2.45.57 3.57a1 1 0 0 1-.25 1z"/></svg>
        604-551-8293
      </li>
      <li>
        <svg viewBox="0 0 24 24" fill="none" stroke="var(--accent)" stroke-width="2"><rect x="3" y="5" width="18" height="14" rx="1"/><path d="M3 6l9 7 9-7"/></svg>
        RWTFittings@mailbox-demo.com
      </li>
      <li>
        <svg viewBox="0 0 24 24" fill="none" stroke="var(--accent)" stroke-width="2"><circle cx="12" cy="12" r="9"/><path d="M3 12h18M12 3c3 3 3 15 0 18M12 3c-3 3-3 15 0 18"/></svg>
        <span>www.<span class="web-domain">rwtfittings-demo</span>.com</span>
      </li>
    </ul>

    <div class="address">
      <span class="address-mark"></span>
      1407-5194 Linden Row Burnaby BC, V5H 2K9
    </div>
  </section>
</main>
</body>
</html>
```